Professional Single Page Website Design for Tollbrook Advisory

Tollbrook Advisory is a new business consultancy specializing in providing expert services to small businesses, primarily in the brick-and-mortar retail and food service sectors. We offer a range of services including franchise development and launch, due diligence, and construction management.

Currently, we have a basic website set up at www.tollbrookadvisory.example, but we need a professional touch to enhance its design and functionality.

Project Requirements:
- Single Page Design: For now, we need a single page design that effectively showcases who we are, our services, and contact information.
- Future Expansion: The design should be flexible and scalable for future expansion to include additional pages like specific service offerings, about us, and a dedicated contact page.
- Design Aesthetic: We are looking for a modern yet professional design that aligns with our brand identity.
- Logo: We have a logo that we like, which was also sourced from Pixel Bazaar. The logo files are attached to this project brief.

Key Sections to Include:
- Hero Section: An engaging introduction to Tollbrook Advisory with a strong visual impact.
- About Us: A brief overview of who we are and our mission.
- Team: Section for the profiles of the two principals.
- Services: A clear and concise presentation of our services, including franchise development, due diligence, and construction management.
- Contact Information: Easy-to-find contact details, including a form for inquiries.
- Call to Action: Encouraging visitors to get in touch with us for consultations or further information.

Design Considerations:
- Ensure the design is responsive and mobile-friendly.
- Include high-quality images and icons that complement our services and industry.
- We do not need development services, this is only a design project.

```html
<!DOCTYPE html>
<html lang="en">
<head>
<meta charset="utf-8">
<title>Tollbrook Advisory — Business Consultancy</title>
<link href="https://fonts.googleapis.com/css2?family=Poppins:wght@300;400;500;600;700&family=Open+Sans:wght@400;600&display=swap" rel="stylesheet">
<style>
:root{
  --ink:#1f2a33;
  --text:#4a4f55;
  --accent:#93c4ad;
  --accent-dark:#7fb49b;
  --paper:#ffffff;
  --mist:#eef3f2;
  --slate:#2c3b47;
  --navy:#0b1826;
  --black:#000000;
  --line:#cfd6d4;
}
*{box-sizing:border-box;margin:0;padding:0}
html,body{width:1200px;height:3244px;overflow:hidden}
body{position:relative;background:var(--paper);font-family:"Poppins",sans-serif;color:var(--text)}
.abs{position:absolute}

/* hero */
.hero{position:absolute;left:0;top:0;width:1200px;height:670px;overflow:hidden}
.hero-shape{position:absolute;inset:0}
.brand{left:111px;top:26px;display:flex;align-items:center;gap:12px;color:#fff;font-weight:600;font-size:22px;line-height:1}
.brand .dot{width:46px;height:46px;border-radius:50%;border:4px solid #fff}
.nav{top:38px;left:0;width:1200px;font-size:15px;color:#fff}
.nav a{position:absolute;color:#fff;text-decoration:none;white-space:nowrap}
.btn{background:var(--accent);color:var(--ink);font-weight:500;text-transform:uppercase;display:flex;align-items:center;justify-content:center;text-decoration:none}
.hero-kicker{left:110px;top:180px;font-size:35px;font-weight:600;color:#fff}
.hero-title{left:108px;top:232px;font-size:84px;font-weight:700;color:#fff;line-height:82px;letter-spacing:-1px}
.slider-dots{top:619px;left:576px;display:flex;gap:8px}
.slider-dots span{width:11px;height:11px;border-radius:50%;border:2px solid #fff}
.slider-dots span.on{background:#fff}

/* about */
.about{left:0;top:560px;width:1200px;height:578px;background:var(--mist);z-index:-1}
.about-title{left:111px;top:742px;font-size:35px;font-weight:500;color:var(--ink);line-height:51px}
.mission{left:111px;top:900px;width:437px;height:155px;background:var(--accent);padding:18px 26px}
.mission h3{font-size:19px;font-weight:500;color:var(--ink);margin-bottom:10px}
.mission p{font-size:14px;line-height:26px;color:#3d4a45;font-weight:300}
.about-copy{left:599px;top:748px;width:492px;font-size:13.8px;line-height:25.7px;font-weight:300;color:#3b4046}
.learn{left:601px;top:975px;font-size:15px;font-weight:500;color:var(--ink);border-bottom:1px solid var(--ink);padding-bottom:2px}

/* services */
.section-title{left:0;width:1200px;text-align:center;font-size:36px;font-weight:500;color:var(--ink)}
.card{width:300px;height:248px;top:1366px;border:1px solid var(--line);background:#fff}
.card-img{position:absolute;left:27px;top:-57px;width:245px;height:119px}
.card h3{position:absolute;top:82px;width:100%;text-align:center;font-size:20.5px;font-weight:500;color:var(--ink);white-space:nowrap}
.card p{position:absolute;top:124px;left:16px;right:16px;text-align:center;font-size:13px;line-height:21.5px;font-weight:300;color:#4a4f55}
.card .btn{position:absolute;top:193px;left:85px;width:129px;height:41px;font-size:13px}
.arrow{top:1478px}

/* team */
.team{left:0;top:1710px;width:1200px;height:600px;background:linear-gradient(160deg,#33424e,#26333d 60%,#2f3e49)}
.team-title{top:1768px;color:#fff}
.photo{position:absolute}
.profile{top:2010px;width:349px;height:242px;background:var(--accent);padding:22px 20px;font-family:"Open Sans",sans-serif;color:#2b3530}
.profile h3{font-family:"Poppins",sans-serif;font-size:27px;font-weight:500;color:var(--ink);line-height:1.2}
.profile .role{font-size:15px;margin:6px 0 18px}
.profile p{font-size:14.6px;line-height:25.5px}

/* contact */
.contact-item{left:135px;display:flex;gap:24px;align-items:center}
.contact-icon{width:48px;height:48px;border-radius:50%;border:2px solid var(--ink);display:flex;align-items:center;justify-content:center}
.contact-item h4{font-size:16px;font-weight:400;color:var(--ink);text-transform:uppercase}
.contact-item span{font-size:14px;font-weight:300;color:#666}
.field{border-bottom:1px solid #8a8f94;font-size:14px;color:#333;padding:0 5px 18px}
.submit{left:541px;top:2698px;width:151px;height:50px;font-size:16px}

/* footer */
.footer-shape{left:0;top:2830px;width:1200px;height:414px}
.foot-brand{left:0;top:2910px;width:1200px;display:flex;flex-direction:column;align-items:center;gap:8px;color:#fff;font-size:18px;line-height:26px}
.foot-brand .dot{width:88px;height:88px;border-radius:50%;border:7px solid var(--accent)}
.foot-nav a{position:absolute;top:3058px;color:#fff;font-size:14px;text-decoration:none;transform:translateX(-50%);white-space:nowrap}
.social{top:3106px;left:496px;display:flex;gap:7px}
.social span{width:36px;height:36px;border-radius:50%;border:1.5px solid #fff}
.foot-rule{left:111px;top:3170px;width:978px;height:1px;background:#2a2a2a}
.copy{left:0;top:3198px;width:1200px;text-align:center;font-size:13.5px;color:#fff}
.copy a{color:var(--accent)}
</style>
</head>
<body>

<header class="hero">
  <svg class="hero-shape" width="1200" height="670" viewBox="0 0 1200 670">
    <defs>
      <linearGradient id="heroFill" x1="0" y1="0" x2="1" y2="0.6">
        <stop offset="0" stop-color="#050b12"/>
        <stop offset="0.35" stop-color="#0c2338"/>
        <stop offset="0.7" stop-color="#1670a8"/>
        <stop offset="1" stop-color="#2fc9c4"/>
      </linearGradient>
    </defs>
    <polygon points="1200,600 600,667 1200,642" fill="#d9dedd"/>
    <polygon role="img" aria-label="Hand touching a glowing consulting dashboard with business icons" points="0,0 1200,0 1200,580 600,667 0,577" fill="url(#heroFill)"/>
  </svg>
</header>

<div class="abs brand"><span class="dot"></span>Tollbrook<br>Advisory</div>
<nav class="abs nav">
  <a style="left:509px">Home</a><a style="left:592px">About</a><a style="left:675px">Services</a><a style="left:776px">Team</a><a style="left:857px">Contact</a>
</nav>
<a class="abs btn" style="left:968px;top:28px;width:121px;height:41px;font-size:13px">Get in touch</a>
<div class="abs hero-kicker">Tollbrook Advisory</div>
<h1 class="abs hero-title">Business<br>Consultancy</h1>
<a class="abs btn" style="left:111px;top:430px;width:139px;height:42px;font-size:13px">Consultations</a>
<div class="abs slider-dots"><span></span><span class="on"></span><span></span></div>

<section class="abs about"></section>
<h2 class="abs about-title">About Tollbrook<br>Advisory</h2>
<div class="abs mission">
  <h3>Our Mission</h3>
  <p>Lorem ipsum dolor sit amet, consectetur adipiscing elit, sed do eiusmod tempor incididunt ut labore et dolore magna aliqua.</p>
</div>
<p class="abs about-copy">Welcome to Tollbrook Advisory, your trusted partner in navigating the complexities of the real estate and small business markets. Founded by industry veterans Rafael Quintero and Dale Onishi, we specialize in providing comprehensive services tailored to the unique needs of our clients. Whether you're a franchisee, a new restaurant owner, or a commercial real estate investor, our expertise in due diligence, construction management, and investment property evaluation ensures you make informed, strategic decisions.</p>
<a class="abs learn">Learn More &rarr;</a>

<h2 class="abs section-title" style="top:1222px">Our Services</h2>
<svg class="abs arrow" style="left:66px" width="34" height="26" viewBox="0 0 34 26"><path d="M32 13H3M13 3L3 13l10 10" fill="none" stroke="#999" stroke-width="2"/></svg>
<svg class="abs arrow" style="left:1102px" width="34" height="26" viewBox="0 0 34 26"><path d="M2 13h29M21 3l10 10-10 10" fill="none" stroke="#111" stroke-width="2"/></svg>

<article class="abs card" style="left:113px">
  <div class="card-img" role="img" aria-label="Hand placing small storefront cards beside a laptop" style="background:linear-gradient(135deg,#5a5a5a,#d9d4cc)"></div>
  <h3>Franchise Development</h3>
  <p>Comprehensive franchise setup from evaluation to launch for scalable business growth.</p>
  <a class="btn">Learn more &rarr;</a>
</article>
<article class="abs card" style="left:451px">
  <div class="card-img" role="img" aria-label="Two business silhouettes shaking hands over chess pieces at sunset" style="background:linear-gradient(180deg,#2d5a86,#e9a24b 55%,#1a1a1a)"></div>
  <h3>Due Diligence</h3>
  <p>Conducting thorough due diligence for business and property transactions to identify potential risks and liabilities.</p>
  <a class="btn">Learn more &rarr;</a>
</article>
<article class="abs card" style="left:786px">
  <div class="card-img" role="img" aria-label="Team reviewing construction plans around a table" style="background:linear-gradient(135deg,#c9d3db,#6e87a3)"></div>
  <h3>Construction Management</h3>
  <p>Conducting thorough due diligence for business and property transactions to identify potential risks and liabilities.</p>
  <a class="btn">Learn more &rarr;</a>
</article>

<section class="abs team" role="img" aria-label="Darkened photo of a business meeting"></section>
<h2 class="abs section-title team-title">Our Leadership Team</h2>
<div class="photo" role="img" aria-label="Portrait of Dale Onishi" style="left:111px;top:1862px;width:203px;height:214px;background:linear-gradient(160deg,#9a8468,#4a3a2c)"></div>
<div class="photo" role="img" aria-label="Portrait of Rafael Quintero" style="left:614px;top:1866px;width:196px;height:207px;background:linear-gradient(180deg,#b7c8d6,#e9e6e2)"></div>
<div class="abs profile" style="left:240px">
  <h3>Dale Onishi</h3>
  <div class="role">Principal</div>
  <p>Dale Onishi is a seasoned real estate expert with extensive experience in project and construction management, and a licensed real estate agent in California.</p>
</div>
<div class="abs profile" style="left:739px">
  <h3>Rafael Quintero</h3>
  <div class="role">Principal</div>
  <p>Rafael Quintero brings almost 20 years of rich experience as a real estate investor and a pivotal role at one of southern California's largest real estate</p>
</div>

<h2 class="abs section-title" style="top:2394px">Contact us</h2>
<div class="abs contact-item" style="top:2481px">
  <div class="contact-icon"><svg width="14" height="18" viewBox="0 0 14 18"><path d="M7 1a6 6 0 0 0-6 6c0 4.5 6 10 6 10s6-5.5 6-10a6 6 0 0 0-6-6z" fill="none" stroke="#93c4ad" stroke-width="1.6"/><circle cx="7" cy="7" r="2" fill="#93c4ad"/></svg></div>
  <div><h4>Address</h4><span>214 Meridian Park Way Suite 300</span></div>
</div>
<div class="abs contact-item" style="top:2570px">
  <div class="contact-icon"><svg width="16" height="16" viewBox="0 0 16 16"><path d="M3 1l3 3-2 2c1 2 3 4 5 5l2-2 3 3-2 2C7 14 2 9 1 3z" fill="#93c4ad"/></svg></div>
  <div><h4>Phone</h4><span>+1 555 014 2290</span></div>
</div>
<div class="abs contact-item" style="top:2655px">
  <div class="contact-icon"><svg width="12" height="18" viewBox="0 0 12 18"><rect x="1" y="1" width="10" height="16" rx="2" fill="none" stroke="#93c4ad" stroke-width="1.6"/><circle cx="6" cy="14" r="1" fill="#93c4ad"/></svg></div>
  <div><h4>Email</h4><span>info@tollbrookadvisory.example</span></div>
</div>
<div class="abs field" style="left:541px;top:2490px;width:251px">First Name :</div>
<div class="abs field" style="left:812px;top:2490px;width:251px">Last Name :</div>
<div class="abs field" style="left:541px;top:2558px;width:251px">Email :</div>
<div class="abs field" style="left:812px;top:2558px;width:251px">Phone :</div>
<div class="abs field" style="left:541px;top:2637px;width:522px">Message :</div>
<a class="abs btn submit">Submit</a>

<svg class="abs footer-shape" width="1200" height="414" viewBox="0 0 1200 414">
  <polygon points="0,98 0,60 600,8 600,98" fill="#d9dedd"/>
  <polygon points="0,98 600,8 1200,98 1200,414 0,414" fill="#000"/>
</svg>
<div class="abs foot-brand"><span class="dot"></span>Tollbrook Advisory</div>
<nav class="foot-nav">
  <a style="left:314px">HOME</a><a style="left:448px">ABOUT US</a><a style="left:594px">SERVICES</a><a style="left:724px">TEAM</a><a style="left:861px">CONTACT US</a>
</nav>
<div class="abs social"><span></span><span></span><span></span><span></span><span></span></div>
<div class="abs foot-rule"></div>
<p class="abs copy">©Copyrights 2024 <a>TOLLBROOKADVISORY</a> &nbsp;|&nbsp; All Rights Reserved</p>

</body>
</html>
```